Cozy Cradle Loops Needs a Beautiful Website

I need a new website for this new E-commerce. I sell handmade Cozy Cradle Loops, e.g. booties, headbands, hats, etc. I need a feminine and soft design to make the moms-to-be say 'oohh ahh'. I'd like pink, blue and gray. I'd like an inviting homepage, and nice regular pages where people can see and order the products.

Industry/Entity Type

Baby

Requirements
Must have
• beautiful, soft, feminine design. Please use pictures of the colors I'd like: brown, yellow, pink and blue. Any combination, but definitely include brown.

```html
<!DOCTYPE html>
<html lang="en">
<head>
<meta charset="utf-8">
<title>Cozy Cradle Loops</title>
<link href="https://fonts.googleapis.com/css2?family=Open+Sans:wght@400;600;700&display=swap" rel="stylesheet">
<style>
:root{
  --page:#fdfdfd;
  --brown:#5a3310;
  --brown-dark:#3a1d05;
  --pink:#ec3f95;
  --pink-soft:#f3d5e3;
  --sky:#a9d3f0;
  --sky-deep:#7fb6df;
  --gray:#7a7a7a;
  --gray-line:#e2e2e2;
  --orange:#ef7d1a;
  --gold:#f5b51c;
  --white:#ffffff;
}
*{margin:0;padding:0;box-sizing:border-box}
html,body{width:1066px;height:1200px;overflow:hidden}
body{position:relative;background:var(--page);font-family:"Open Sans",sans-serif;color:var(--gray)}
.abs{position:absolute}
.brand{left:100px;top:58px;font-size:30px;font-weight:700;color:var(--pink);display:flex;align-items:center;gap:10px}
.brand-dot{width:18px;height:18px;border-radius:50%;background:var(--sky-deep)}
.account-links{left:578px;top:98px;font-size:11.5px;color:#666;word-spacing:2px}
.account-links span{margin:0 6px;color:#888}
.cart-divider{left:858px;top:88px;width:1px;height:36px;background:var(--gray-line)}
.cart{left:872px;top:90px;text-align:right;color:var(--brown);line-height:1.1}
.cart small{display:block;font-size:10.5px;font-weight:600}
.cart strong{font-size:15px;font-weight:600}
.cart-icon{left:936px;top:94px}
.ribbon-tail{top:172px}
.nav{left:61px;top:160px;width:945px;height:50px;background:linear-gradient(#b9dcf4,#8fc3e8);box-shadow:0 2px 3px rgba(0,0,0,.15)}
.nav a{position:absolute;top:15px;color:var(--white);font-weight:700;font-size:14.5px;text-decoration:none;text-shadow:0 1px 1px rgba(0,0,0,.2);transform:translateX(-50%)}
.main{left:100px;top:210px;width:866px;height:788px;border:1px solid var(--pink-soft);border-top:none;background:var(--white)}
.hero{left:109px;top:210px;width:849px;height:318px;background:radial-gradient(circle at 22% 40%,#f1e6df 0,#e9d8cc 22%,transparent 38%),linear-gradient(100deg,#e8f2fa 0%,#b9dcf3 45%,#7fb9e8 100%)}
.hero-caption{left:585px;top:293px;width:322px;height:150px;background:rgba(255,255,255,.72);padding:10px 16px}
.hero-caption h2{font-size:24px;font-weight:600;color:var(--brown);line-height:1.3}
.hero-caption p{font-size:15px;color:#666;line-height:1.45;margin-top:4px}
.btn-buy{position:absolute;left:16px;top:100px;width:88px;height:32px;background:var(--gold);border-radius:2px;font-size:13px;color:var(--brown);text-align:center;line-height:32px}
.arrow{top:328px;width:20px;height:80px;background:var(--white)}
.arrow-left{left:109px;border-radius:0 40px 40px 0}
.arrow-right{left:938px;border-radius:40px 0 0 40px}
.arrow svg{position:absolute;top:34px}
.intro{left:109px;top:552px;width:849px;text-align:center}
.intro h3{font-size:21px;font-weight:600;color:var(--brown)}
.intro p{font-size:14px;line-height:22px;margin:6px auto 0;width:660px}
.rule{left:109px;top:663px;width:849px;height:1px;background:var(--gray-line)}
.products-title{left:109px;top:690px;width:849px;text-align:center;font-size:27px;font-weight:600;color:var(--brown)}
.tabs{left:109px;top:734px;width:849px;text-align:center;font-size:14px;color:var(--pink)}
.tabs span{margin:0 9px;color:#999}
.tab-mark{left:390px;top:754px;width:56px;height:3px;background:var(--pink)}
.tab-tip{left:412px;top:756px;width:0;height:0;border-left:6px solid transparent;border-right:6px solid transparent;border-top:6px solid var(--pink)}
.card{top:788px;width:156px;height:189px;border:1px solid #dcdcdc;background:var(--white);text-align:center}
.card-photo{margin:3px;height:127px}
.card h4{font-size:13px;font-weight:600;color:#333;margin-top:11px}
.card p{font-size:10.5px;color:#555;margin-top:2px}
.newsletter-label{left:187px;top:1021px;font-size:22px;color:var(--orange);font-weight:400}
.field{top:1020px;width:182px;height:28px;border:1px solid #ccc;background:var(--white);font-size:12px;color:#888;padding:6px 12px}
.btn-subscribe{left:803px;top:1020px;width:75px;height:28px;background:var(--orange);color:var(--white);font-size:12.5px;font-weight:600;text-align:center;line-height:28px}
.footer{left:0;top:1074px;width:1066px;height:126px;background:linear-gradient(#3f1f05,#2e1604)}
.footer-nav{left:0;top:1097px;width:1066px;text-align:center;font-size:12px;color:#eee}
.footer-nav a{color:#eee;text-decoration:none;margin:0 16px}
.footer-nav a::before{content:"• ";font-size:10px}
.footer-rule{left:100px;top:1134px;width:866px;height:1px;background:#5a3a1c}
.copyright{left:101px;top:1157px;font-size:12px;color:#eee;word-spacing:2px}
.social{top:1153px;width:26px;height:26px;border-radius:50%}
</style>
</head>
<body>
<div class="abs brand"><span class="brand-dot"></span>Cozy Cradle Loops</div>

<div class="abs account-links">My Account<span>/</span>My Wishlist<span>/</span>Checkout<span>/</span>Log in</div>
<div class="abs cart-divider"></div>
<div class="abs cart" style="width:56px"><small>My Cart</small><strong>0 items</strong></div>
<svg class="abs cart-icon" width="30" height="26" viewBox="0 0 30 26" aria-hidden="true">
  <path d="M9 10 L15 2 L21 10" fill="none" stroke="#5a3310" stroke-width="2"/>
  <path d="M2 10 H28 L24 24 H6 Z" fill="#5a3310"/>
  <path d="M9 13 V21 M13 13 V21 M17 13 V21 M21 13 V21" stroke="#fff" stroke-width="1.5"/>
</svg>

<svg class="abs ribbon-tail" style="left:10px" width="51" height="54" viewBox="0 0 51 54" aria-hidden="true">
  <path d="M0 0 H51 V50 H0 L14 25 Z" fill="#9ccbec"/>
  <path d="M51 38 V50 H40 Z" fill="#5f93bd"/>
</svg>
<svg class="abs ribbon-tail" style="left:1006px" width="51" height="54" viewBox="0 0 51 54" aria-hidden="true">
  <path d="M51 0 H0 V50 H51 L37 25 Z" fill="#9ccbec"/>
  <path d="M0 38 V50 H11 Z" fill="#5f93bd"/>
</svg>
<nav class="abs nav">
  <a style="left:84px">HOME</a>
  <a style="left:195px">ABOUT US</a>
  <a style="left:323px">PRODUCTS</a>
  <a style="left:467px">TESTIMONIALS</a>
  <a style="left:617px">CONTACT US</a>
  <a style="left:749px">REGISTER</a>
  <a style="left:859px">LOGIN</a>
</nav>

<div class="abs main"></div>

<div class="abs hero" role="img" aria-label="Photo of an expectant mother holding small blue crocheted booties against a soft blue bokeh background"></div>
<div class="abs hero-caption">
  <h2>Nullam dictum aliquam</h2>
  <p>Duis semper blandit nibh, vitae tincidunt tellus scelerisque quis.</p>
  <div class="btn-buy">BUY NOW</div>
</div>
<div class="abs arrow arrow-left"><svg style="left:2px" width="10" height="12" viewBox="0 0 10 12" aria-hidden="true"><path d="M8 1 L2 6 L8 11" fill="none" stroke="#333" stroke-width="2.5"/></svg></div>
<div class="abs arrow arrow-right"><svg style="left:8px" width="10" height="12" viewBox="0 0 10 12" aria-hidden="true"><path d="M2 1 L8 6 L2 11" fill="none" stroke="#333" stroke-width="2.5"/></svg></div>

<div class="abs intro">
  <h3>Nullam ante purus, placerat imperdiet</h3>
  <p>Suspendisse pulvinar faucibus tincidunt. Suspendisse scelerisque, ante eget lobortis dignissim, ipsum ipsum lacinia arcu, lacinia tincidunt magna sapien ornare nisi.</p>
</div>
<div class="abs rule"></div>

<h2 class="abs products-title">OUR PRODUCTS</h2>
<div class="abs tabs">BOOTIES<span>/</span>HEADBANDS<span>/</span>HATS<span>/</span>MORE</div>
<div class="abs tab-mark"></div>
<div class="abs tab-tip"></div>

<div class="abs card" style="left:111px"><div class="card-photo" role="img" aria-label="Black and white crocheted sneaker booties" style="background:linear-gradient(135deg,#9a9a9a,#2a2a2a 60%,#cfcfcf)"></div><h4>Bootie</h4><p>Morbi porttitoreu</p></div>
<div class="abs card" style="left:283px"><div class="card-photo" role="img" aria-label="Brown crocheted sneaker booties with pink star" style="background:linear-gradient(135deg,#a05a8a,#6e5a48 45%,#e8e4df)"></div><h4>Bootie</h4><p>Morbi porttitoreu</p></div>
<div class="abs card" style="left:455px"><div class="card-photo" role="img" aria-label="Cream crocheted sandals with pink flowers" style="background:linear-gradient(135deg,#d8d4c8,#c6bfae 50%,#a89e90)"></div><h4>Bootie</h4><p>Morbi porttitoreu</p></div>
<div class="abs card" style="left:627px"><div class="card-photo" role="img" aria-label="Pink crocheted slippers with roses and ribbon" style="background:linear-gradient(135deg,#e9e4e6,#e9b7cb 55%,#d8d2d4)"></div><h4>Bootie</h4><p>Morbi porttitoreu</p></div>
<div class="abs card" style="left:799px"><div class="card-photo" role="img" aria-label="Red crocheted mary jane booties with white flowers" style="background:linear-gradient(135deg,#d8221f,#b3151a 60%,#8c0f12)"></div><h4>Bootie</h4><p>Morbi porttitoreu</p></div>

<div class="abs newsletter-label">NEWSLETTER SIGNUP</div>
<div class="abs field" style="left:423px">Name</div>
<div class="abs field" style="left:614px">E-mail</div>
<div class="abs btn-subscribe">Subscribe</div>

<footer class="abs footer"></footer>
<nav class="abs footer-nav"><a>Home</a><a>About us</a><a>Products</a><a>Testimonials</a><a>Contact us</a><a>Register</a><a>Login</a></nav>
<div class="abs footer-rule"></div>
<div class="abs copyright">Copyright © 2014 Cozy Cradle Loops. All rights reserved.</div>
<div class="abs social" style="left:904px;background:#3b5b9a" aria-label="Social profile"></div>
<div class="abs social" style="left:938px;background:#3bb3e6" aria-label="Social profile"></div>
</body>
</html>
```